Los Angeles based Demolition, Grading, and Structural concrete Contractor in need of a Sale brochure

We are a Los Angeles-based demolition, grading, and structural concrete contractor looking for a professionally designed sales brochure that represents our company and services. The brochure should be visually appealing, easy to read, and include the following:

-Company Logo: Prominently displayed to enhance brand identity.

-Services We Offer: A clear breakdown of our key services, including demolition, grading, and structural concrete work.

-Project Scope & Capabilities: A brief explanation of the type of projects we handle (residential, commercial, industrial).

-Pricing Information: Mention that demolition services start at $20,000. This price includes complete demolition of structure, safe debris removal and hauling, site preparation for new construction.

-Contact Information: Our phone number(818.502.6617), email(contact@brovanbuildersinc.example) , and website for potential clients to reach out.

The design should reflect the professionalism and strength of our industry, using a modern, clean layout with bold colors that align with construction and demolition themes. Images of past work or stock photos representing our services are encouraged.

Final deliverables should be print-ready (PDF) and digital-friendly formats. Looking forward to creative and impactful designs!

```html
<!DOCTYPE html>
<html lang="en">
<head>
<meta charset="UTF-8">
<title>Brovan Builders — Services Brochure</title>
<link href="https://fonts.googleapis.com/css2?family=Poppins:wght@400;600;700;800&display=swap" rel="stylesheet">
<style>
  :root {
    --brand-blue: #1b75bb;
    --ink: #111111;
    --paper: #ffffff;
    --photo-sky: #c9d3cf;
    --photo-tree: #4f6a3a;
    --photo-ground: #a88b62;
  }
  * { margin: 0; padding: 0; box-sizing: border-box; }
  html, body { width: 1200px; height: 849px; overflow: hidden; background: var(--paper); }
  body { font-family: "Poppins", sans-serif; color: var(--ink); }
  .brochure { position: relative; width: 1200px; height: 849px; overflow: hidden; background: var(--paper); }

  .brand-name {
    position: absolute; left: 39px; top: 52px;
    font-family: "Poppins", sans-serif; font-weight: 700;
    font-size: 30px; letter-spacing: 1px; color: var(--brand-blue);
    line-height: 1;
  }

  .hero-band {
    position: absolute; left: 647px; top: 26px; width: 529px; height: 303px;
    background: var(--brand-blue);
    border-bottom-left-radius: 170px;
  }
  .hero-photo {
    position: absolute; left: 672px; top: 0; width: 528px; height: 303px;
    border-bottom-left-radius: 140px;
    background: linear-gradient(180deg, var(--photo-sky) 0%, var(--photo-tree) 40%, #6b6a4a 70%, var(--photo-ground) 100%);
  }

  .section-title {
    font-family: "Poppins", sans-serif; font-weight: 800;
    color: var(--brand-blue); text-transform: uppercase;
    font-size: 50px; line-height: 48px; letter-spacing: 0.5px;
  }
  .services-title { position: absolute; left: 37px; top: 222px; }
  .scope-title { position: absolute; left: 714px; top: 408px; }

  .timeline { position: absolute; list-style: none; }
  .timeline::before {
    content: ""; position: absolute; left: -19px; top: 4px; bottom: 30px;
    width: 2px; background: var(--brand-blue);
  }
  .timeline li { position: relative; }
  .timeline li::before {
    content: ""; position: absolute; left: -24px; top: 4px;
    width: 11px; height: 11px; border-radius: 50%; background: var(--brand-blue);
  }
  .timeline strong { font-weight: 700; }

  .services-list { left: 67px; top: 299px; font-size: 21.5px; line-height: 27.5px; }
  .services-list li { margin-bottom: 19px; }

  .scope-list { left: 717px; top: 540px; font-size: 21px; line-height: 27.5px; width: 470px; }
  .scope-list li { margin-bottom: 21px; }

  .price-band {
    position: absolute; left: 0; top: 581px; width: 654px; height: 176px;
    background: var(--brand-blue); color: var(--paper);
    border-top-right-radius: 90px; border-bottom-right-radius: 90px;
    padding: 31px 0 0 43px;
  }
  .price-headline { font-weight: 700; font-size: 24.5px; line-height: 30px; text-transform: uppercase; }
  .price-detail { margin-top: 9px; font-size: 20.5px; line-height: 25.5px; width: 470px; }
</style>
</head>
<body>
<main class="brochure">
  <div class="brand-name">BROVAN BUILDERS</div>

  <div class="hero-band"></div>
  <div class="hero-photo" role="img" aria-label="Excavator clearing debris and tree stumps on a hillside site with a white fence and eucalyptus trees"></div>

  <h2 class="section-title services-title">Our Services</h2>
  <ul class="timeline services-list">
    <li><strong>Demolition:</strong> Safe, efficient removal of<br>structures with minimal disruption.</li>
    <li><strong>Grading:</strong> Precision land leveling for<br>stable foundations and optimal drainage.</li>
    <li><strong>Structural Concrete:</strong> Durable, high-quality<br>concrete solutions for all types of projects.</li>
  </ul>

  <section class="price-band">
    <h3 class="price-headline">Demolition services start at $20,000</h3>
    <p class="price-detail">This price includes complete demolition of structure, safe debris removal and hauling, site preparation for new construction.</p>
  </section>

  <h2 class="section-title scope-title">Project Scope<br>&amp; Capabilities</h2>
  <ul class="timeline scope-list">
    <li><strong>Residential:</strong> Foundations, driveways,<br>retaining walls, and more.</li>
    <li><strong>Commercial:</strong> Parking lots, office<br>buildings, and large-scale site work.</li>
    <li><strong>Industrial:</strong> Heavy-duty concrete<br>structures, warehouses, and specialized<br>projects.</li>
  </ul>
</main>
</body>
</html>
```